Website art for a private investigator.

The purposed graphic is for a business website ( brellwick.com ). The business name is “Harrowgate & Associates ltd.” This firm is a private investigation agency. The purposed graphic will be placed in the upper most main area of the main page of the website. If you look at the website now there is no graphic.

I have an idea of what I am looking for. I imagine a graphic depicting a contemporary private investigator walking through a dark alley searching for some unknown item. This is symbolic of private investigators hired to find information for people who their selfs do not have the know how nor could they handle the complexity and high stress environment. When I say contemporary I am referring to todays private investigators typically highly educated and well dressed.

Target Market(s)

People who need a private investigator

Industry/Entity Type

Business

Requirements
Must have
• match website; I have an idea of what I am looking for. I imagine a graphic depicting a contemporary private investigator walking through a dark alley searching for some unknown item. This is symbolic of private investigators hired to find information for people who their selfs do not have the know how nor could they handle the complexity and high stress environment. When I say contemporary I am referring to todays private investigators typically highly educated and well dressed.
Should not have
• Everyone please understand, I am not looking for a new website. I am only looking for the image. If you have submitted a design and its displayed on another website other than mine. I will not select your design. I am sorry for being harsh, but I asked for the image to match my website.

```html
<!DOCTYPE html>
<html lang="en">
<head>
<meta charset="utf-8">
<title>Harrowgate &amp; Associates ltd. — Private Investigation</title>
<link href="https://fonts.googleapis.com/css2?family=Montserrat:wght@400;600;700&family=Open+Sans:wght@300;400;600;700&display=swap" rel="stylesheet">
<style>
:root{
  --ink:#1b1b1b;
  --text:#555;
  --muted:#888;
  --blue:#1f64b0;
  --blue-dark:#174f8e;
  --call:#2a78c8;
  --red:#b8322a;
  --nav:#222;
  --soft:#ececec;
  --white:#fff;
  --rule:#dcdcdc;
}
*{box-sizing:border-box;margin:0;padding:0}
html,body{width:1200px;height:2268px;overflow:hidden}
body{background:var(--white);font-family:"Open Sans",Arial,sans-serif;color:var(--text);position:relative}
.abs{position:absolute}

/* header */
.site-header{left:0;top:0;width:1200px;height:120px;background:var(--white)}
.brand{left:24px;top:10px;width:250px;height:100px;background:var(--ink);display:flex;align-items:center;gap:14px;padding:0 18px}
.brand-square{width:16px;height:16px;background:var(--white);flex:none}
.brand-name{color:var(--white);font-family:"Montserrat",sans-serif;font-weight:700;font-size:17px;line-height:1.25;letter-spacing:.5px}
.call{right:40px;top:40px;font-family:"Montserrat",sans-serif;font-size:34px;color:var(--call);letter-spacing:1px}
.call b{font-weight:600;font-size:26px;margin-right:6px}

/* nav */
.main-nav{left:0;top:120px;width:1200px;height:34px;background:var(--nav);display:flex;align-items:center;padding:0 40px}
.main-nav a{color:#ddd;text-decoration:none;font-size:12px;font-weight:600;letter-spacing:.5px;margin-right:54px}
.social{margin-left:auto;display:flex;gap:10px}
.social span{width:14px;height:14px;border-radius:50%;background:#777}

/* hero */
.hero{left:0;top:154px;width:1200px;height:486px;background:linear-gradient(90deg,#1a1a1a 0%,#2b2b2b 40%,#4a4a4a 62%,#2a2a2a 80%,#161616 100%)}
.hero-kicker{left:120px;top:224px;color:var(--white);font-size:26px;font-weight:400}
.hero-title{left:120px;top:262px;color:var(--white);font-size:56px;font-weight:300;line-height:1.05}
.btn{background:var(--blue);color:var(--white);font-size:14px;font-weight:600;text-align:center;line-height:44px;height:44px;width:130px;display:block}
.hero .btn{position:absolute;left:120px;top:326px}

/* services */
.section-title{width:1200px;left:0;text-align:center;font-family:"Montserrat",sans-serif;font-size:24px;color:var(--ink);letter-spacing:1px}
.section-title b{font-weight:700}
.section-title span{font-weight:400}
.services-title{top:690px}
.lead{left:250px;width:700px;text-align:center;font-size:13px;line-height:1.6}
.services-lead{top:730px}
.service{top:810px;width:330px;height:160px;display:flex;gap:16px}
.service-photo{width:150px;height:150px;border-radius:50%;border:6px solid #f1f1f1;flex:none}
.service h3{color:var(--red);font-size:20px;font-weight:600;line-height:1.1;margin:14px 0 10px}
.service p{font-size:11px;line-height:1.55;color:var(--muted)}

/* what we do */
.what{left:0;top:1100px;width:1200px;height:320px;background:linear-gradient(180deg,#f1f1f1,#e4e4e4)}
.what-title{top:1160px}
.what-lead{top:1200px;left:230px;width:740px}
.what .btn{position:absolute;left:535px;top:206px}

/* two columns */
.col-title{font-size:21px;color:var(--ink);font-weight:400}
.rates{left:120px;top:1470px;width:520px}
.rates .sub{font-size:13px;color:var(--blue-dark);margin:8px 0 16px}
.rates p{font-size:12.5px;line-height:1.6;margin-bottom:14px}
.reviews{left:700px;top:1450px;width:400px}
.reviews .col-title{line-height:1.3;margin-bottom:18px}
.review{display:flex;gap:16px;margin-bottom:22px}
.avatar{width:58px;height:58px;border-radius:50%;background:#6b5a4b;flex:none}
.review p{font-size:12px;line-height:1.5}
.review cite{display:block;font-style:normal;font-size:12px;margin-top:2px}
.review cite b{color:var(--ink)}

/* footer */
.site-footer{left:0;top:1920px;width:1200px;height:300px;background:var(--blue)}
.footer-brand{left:120px;top:40px;width:200px;height:120px;background:var(--ink);display:flex;align-items:center;gap:12px;padding:0 16px}
.footer-brand .brand-name{font-size:15px}
.f-col{top:40px;color:var(--white)}
.f-col h4{font-size:15px;font-weight:600;letter-spacing:.5px;padding-bottom:8px;border-bottom:1px solid rgba(255,255,255,.35);margin-bottom:12px}
.f-col li{list-style:none;font-size:13px;line-height:1.6}
.f-col p{font-size:13px;line-height:1.55}
.map{width:260px;height:170px;background:linear-gradient(135deg,#e8e4d8,#cfd8c8 55%,#d8d2bd)}
.legal{left:0;top:2220px;width:1200px;height:48px;background:#171717;color:#bbb;font-size:12px;text-align:center;line-height:48px}
</style>
</head>
<body>

<header class="site-header abs">
  <div class="brand abs"><span class="brand-square"></span><span class="brand-name">HARROWGATE &amp;<br>Associates ltd.</span></div>
  <div class="call abs"><b>CALL</b>123.456.789</div>
</header>

<nav class="main-nav abs">
  <a href="#">MAIN</a><a href="#">INVESTIGATION &amp; ANALYSIS</a><a href="#">NEWS</a><a href="#">FEES</a>
  <div class="social"><span></span><span></span><span></span><span></span><span></span></div>
</nav>

<section class="hero abs" role="img" aria-label="Well dressed investigator with a magnifying glass and notebook in a dark alley">
  <div class="hero-kicker abs" style="left:120px;top:70px">Solution For Private</div>
  <h1 class="hero-title abs" style="left:120px;top:108px">Investigation &amp;<br>Analysis Firm</h1>
  <a class="btn" href="#">Read More</a>
</section>

<h2 class="section-title services-title abs"><span>HARROWGATE</span> <b>SERVICES</b></h2>
<p class="lead services-lead abs">Discreet and thorough private inquiries for families, lawyers and businesses, handled by trained and licensed investigators. Every case is kept confidential, documented with care and reported in clear, plain language you can act on.</p>

<div class="service abs" style="left:100px">
  <div class="service-photo" role="img" aria-label="Hands in handcuffs"style="background:#c7a48c"></div>
  <div><h3>Criminal<br>Defense</h3><p>Evidence review and witness interviews that support your defense team in court.</p></div>
</div>
<div class="service abs" style="left:450px">
  <div class="service-photo" role="img" aria-label="Gavel on a desk" style="background:#8a6a4e"></div>
  <div><h3>Legal<br>Investigation</h3><p>Background checks, records searches and fact finding for civil matters.</p></div>
</div>
<div class="service abs" style="left:800px">
  <div class="service-photo" role="img" aria-label="Camera lens close up" style="background:#3d3d3d"></div>
  <div><h3>Forensic<br>Photography</h3><p>Scene and detail photographs taken to a standard fit for evidence.</p></div>
</div>

<section class="what abs" role="img" aria-label="Faint city background">
</section>
<h2 class="section-title what-title abs"><span>WHAT WE DO</span> <b>HARROWGATE</b></h2>
<p class="lead what-lead abs">Lorem Ipsum is simply dummy text of the printing and typesetting industry. Lorem Ipsum has been the industry's standard dummy text ever since the 1500s, when an unknown printer took a galley of type and scrambled it to make a type specimen book. It has survived not only five centuries, but also the leap into electronic typesetting, remaining essentially unchanged. It was popularised in the 1960s with the release of Letraset sheets.</p>
<a class="btn abs" href="#" style="left:535px;top:1306px">Read More</a>

<section class="rates abs">
  <h2 class="col-title">How Much Do We Charge</h2>
  <p class="sub">Clear, fixed rates agreed before any work on your case begins.</p>
  <p>We believe the cost of a private investigation should be known from the first call. After a free consultation we outline the scope of work, the hours we expect to need and any travel or filing costs, so there are no surprises when the report arrives.</p>
  <p>Our investigators use field work, public records and careful interviews to build a complete picture. Simple searches are billed at a flat fee, while surveillance and complex matters are billed by the hour with a written estimate and regular updates.</p>
  <p>Retainers are held in trust and any unused balance is returned at the close of the case. Ask us about payment plans for families.</p>
</section>

<aside class="reviews abs">
  <h2 class="col-title">Ohio and West Virginia Private Investigators</h2>
  <div class="review"><div class="avatar" role="img" aria-label="Client portrait"></div><div><p>Fast, discreet and professional. They found what we needed in days.</p><cite><b>John Doe</b> Director of company</cite></div></div>
  <div class="review"><div class="avatar" role="img" aria-label="Client portrait" style="background:#5d5248"></div><div><p>Clear reports and honest advice from the very first meeting.</p><cite><b>John Doe</b> Director of company</cite></div></div>
  <div class="review"><div class="avatar" role="img" aria-label="Client portrait" style="background:#7a6655"></div><div><p>Their evidence made all the difference for our legal team.</p><cite><b>John Doe</b> Director of company</cite></div></div>
  <div class="review"><div class="avatar" role="img" aria-label="Client portrait" style="background:#4f463e"></div><div><p>Calm, careful people who kept us informed at every step.</p><cite><b>John Doe</b> Director of company</cite></div></div>
</aside>

<footer class="site-footer abs">
  <div class="footer-brand abs"><span class="brand-square"></span><span class="brand-name">HARROWGATE &amp;<br>Associates ltd.</span></div>
  <div class="f-col abs" style="left:380px;width:150px">
    <h4>LINKS</h4>
    <ul><li>Labor Dispute</li><li>Accidents</li><li>Negligence</li><li>Employment Accident</li><li>Product Liability</li><li>Equity Matters</li><li>Missing Person</li></ul>
  </div>
  <div class="f-col abs" style="left:560px;width:210px">
    <h4>CONTACT US</h4>
    <p>HARROWGATE ASSOCIATES<br>P.O. Box 412<br>Dunmore Falls, Ohio 45000</p>
    <p style="margin-top:14px">Phone: (555) 014-2280<br>Fax: (555) 014-2281<br>brellwick.com</p>
  </div>
  <div class="f-col abs" style="left:820px;width:260px">
    <h4>HOW TO FIND US</h4>
    <div class="map" role="img" aria-label="Street map showing the office location"></div>
  </div>
</footer>
<div class="legal abs">© 2012-2014 Harrowgate &amp; Associates ltd. All rights reserved</div>

</body>
</html>
```